KAJU Freightways #ALLKAJU Business Cards & Letterhead

I am looking to business cards designed for our organization. We are currently undergoing a small re-branding that is taking place. Our organization is called KAJU Freightways and we are headquartered in Phoenix, AZ. We primarily provide transportation and logistics services to the Marlow Parcel Bureau who is our largest customer. I would like to see a design that incorporates name, title, contact info, website, and address (this will be different depending on the employee). I would also like to see some color on the business card using our logo colors or a variation. I would like our logo on the back of the business card with the website displayed. The final design should communicate that we are a next generation transportation operate that focuses on being driver-first, customer-centric, innovative, and sustainable.We would also like our #ALLKAJU catch phrase incorporated as well.

Target Market(s)

Transportation & Logistics

Industry/Entity Type

Trucking Company

Contact Information for Business Card

-First and Last Name
-Position Title
-Contact Phone
-Contact Email
-Physical Address

Font styles to use
Serif

Colors

Designer to choose colors to be used in the design.

Requirements
Must have
• -KAJU logo prominently displayed
• -#ALLKAJU catch phrase used
• -Some amount of color, design gradient, etc.
• -Logo on the back with website listed (https://www.kajufreightco.example)

```html
<!DOCTYPE html>
<html lang="en">
<head>
<meta charset="utf-8">
<title>KAJU Freightways Business Card</title>
<link rel="stylesheet" href="https://fonts.googleapis.com/css2?family=Roboto+Serif:opsz,wght@8..144,300;8..144,400;8..144,500;8..144,700&display=swap">
<style>
  :root {
    --teal: #053845;
    --teal-light: #0b4553;
    --green: #7dc142;
    --white: #ffffff;
    --backdrop: #dcdcdc;
  }
  * { box-sizing: border-box; margin: 0; padding: 0; }
  html, body {
    width: 1125px; height: 1200px; overflow: hidden;
    background: var(--backdrop);
    font-family: "Roboto Serif", Georgia, serif;
  }
  .canvas { position: relative; width: 1125px; height: 1200px; }
  .card {
    position: absolute; left: 162px; width: 800px; height: 457px;
    border-radius: 24px; overflow: hidden;
  }
  .card--front { top: 98px; background: var(--white); }
  .card--back { top: 630px; background: var(--teal); }

  .brand-mark {
    position: absolute; left: 50%; transform: translate(-50%, -50%);
    border-radius: 50%; border-style: solid; border-color: var(--green);
    display: flex; align-items: center; justify-content: center;
  }
  .brand-mark__name { font-weight: 700; letter-spacing: 0; line-height: 1; }
  .card--front .brand-mark { top: 142px; width: 208px; height: 208px; border-width: 5px; }
  .card--front .brand-mark__name { color: var(--teal); font-size: 54px; }
  .card--back .brand-mark { top: 210px; width: 264px; height: 264px; border-width: 7px; }
  .card--back .brand-mark__name { color: var(--white); font-size: 68px; }

  .rule-green { position: absolute; left: 0; width: 100%; top: 272px; height: 6px; background: var(--green); }
  .contact-band { position: absolute; left: 0; width: 100%; top: 280px; height: 125px; background: var(--teal); }
  .address-band {
    position: absolute; left: 0; width: 100%; top: 411px; height: 46px; background: var(--green);
    color: var(--white); font-size: 18px; font-weight: 300;
    display: flex; align-items: center; justify-content: center;
  }
  .person { position: absolute; right: 428px; top: 30px; text-align: right; }
  .person__name { color: var(--green); font-size: 26px; font-weight: 500; line-height: 1.15; }
  .person__title { color: var(--white); font-size: 18px; font-weight: 300; margin-top: 4px; }
  .divider { position: absolute; left: 393px; top: 24px; width: 1px; height: 78px; background: var(--white); opacity: .8; }
  .contact-list { position: absolute; left: 422px; top: 23px; list-style: none; }
  .contact-list li {
    display: flex; align-items: center; gap: 10px; height: 25px;
    color: var(--white); font-size: 17px; font-weight: 300; white-space: nowrap;
  }
  .contact-list svg { width: 16px; height: 16px; fill: var(--green); flex: none; }
  .accent { color: var(--green); }

  .world-map {
    position: absolute; left: 0; top: 0; width: 100%; height: 100%;
    background: radial-gradient(ellipse 60% 45% at 55% 45%, var(--teal-light), var(--teal) 80%);
  }
  .back-tagline {
    position: absolute; left: 0; width: 100%; top: 362px; text-align: center;
    color: var(--green); font-size: 22px; font-weight: 700; letter-spacing: 2px;
  }
  .back-web {
    position: absolute; left: 0; width: 100%; top: 400px; text-align: center;
    color: var(--white); font-size: 17px; font-weight: 300;
  }
</style>
</head>
<body>
<main class="canvas">
  <section class="card card--front" aria-label="Business card front">
    <div class="brand-mark"><span class="brand-mark__name">KAJU</span></div>
    <div class="rule-green"></div>
    <div class="contact-band">
      <div class="person">
        <p class="person__name">Dana Whitlow</p>
        <p class="person__title">Manager</p>
      </div>
      <div class="divider"></div>
      <ul class="contact-list">
        <li>
          <svg viewBox="0 0 16 16" aria-hidden="true"><path d="M3.2 1.2l2.3 2.6-1.3 1.8c.9 2 2.4 3.6 4.4 4.6l1.8-1.3 2.6 2.3-1.2 2.2C6.6 13.6 2.3 9.4 1 4.2z"/></svg>
          602-555-0148
        </li>
        <li>
          <svg viewBox="0 0 16 16" aria-hidden="true"><path d="M1 3.5h14v9H1z M1.8 4.2L8 9l6.2-4.8" stroke="#053845" stroke-width="1"/></svg>
          info@kajufreightco.example
        </li>
        <li>
          <svg viewBox="0 0 16 16" aria-hidden="true"><circle cx="8" cy="8" r="7"/><path d="M1 8h14M8 1c-2.5 3-2.5 11 0 14M8 1c2.5 3 2.5 11 0 14" stroke="#053845" stroke-width="1" fill="none"/></svg>
          <span>www.<span class="accent">kajufreightco</span>.example</span>
        </li>
      </ul>
    </div>
    <div class="address-band">4170 North Copper Ridge Road, Phoenix, AZ 85016</div>
  </section>

  <section class="card card--back" aria-label="Business card back">
    <div class="world-map" role="img" aria-label="Faint dotted world map background"></div>
    <div class="brand-mark"><span class="brand-mark__name">KAJU</span></div>
    <p class="back-tagline">#ALLKAJU</p>
    <p class="back-web">www.kajufreightco.example</p>
  </section>
</main>
</body>
</html>
```